Realty Group Needs Classy, Contemporary Letterhead Design

We need a letterhead design for a new realty company located in NY, USA. We buy investment properties to rehabilitate and or keep in our rental portfolio.

```html
<!DOCTYPE html>
<html lang="en">
<head>
<meta charset="utf-8">
<title>Northvale Realty Group – Letterhead</title>
<link rel="stylesheet" href="https://fonts.googleapis.com/css2?family=Montserrat:wght@400;600;800&display=swap">
<style>
  :root {
    --purple: #4f2d86;
    --grey-line: #8a8a8a;
    --text: #333333;
    --muted: #555555;
    --paper: #ffffff;
    --backdrop: #e9e9ea;
    --signature-fill: #eeeeee;
  }
  * { box-sizing: border-box; margin: 0; padding: 0; }
  html, body { width: 1200px; height: 874px; overflow: hidden; background: var(--backdrop); }
  body { font-family: "Montserrat", Arial, sans-serif; color: var(--text); }

  .letterhead {
    position: absolute; left: 310px; top: 12px;
    width: 580px; height: 850px;
    background: var(--paper);
    box-shadow: 0 4px 18px rgba(0,0,0,0.12);
    overflow: hidden;
  }

  .brand { position: absolute; left: 44px; top: 58px; width: 230px; }
  .brand-name {
    font-weight: 800; font-size: 30px; letter-spacing: 0.5px;
    color: var(--purple); line-height: 1; text-transform: uppercase;
  }
  .brand-sub {
    font-weight: 800; font-size: 11px; color: var(--purple);
    letter-spacing: 1.5px; margin-top: 6px; text-align: right;
  }
  .brand-rule { margin-top: 6px; height: 1px; background: var(--grey-line); width: 100%; }

  .divider {
    position: absolute; left: 300px; top: 44px; width: 1px; height: 70px;
    background: var(--grey-line);
  }

  .contact {
    position: absolute; left: 314px; top: 44px;
    font-size: 9.5px; line-height: 13.5px; color: var(--muted);
    list-style: none;
  }
  .contact li { display: flex; align-items: center; gap: 5px; }
  .contact svg { width: 8px; height: 8px; fill: var(--purple); flex: none; }

  .recipient {
    position: absolute; left: 44px; top: 178px;
    font-size: 10.5px; line-height: 14px;
  }

  .body-copy {
    position: absolute; left: 44px; top: 252px; width: 470px;
    font-size: 10.5px; line-height: 15px;
  }
  .body-copy p { margin-bottom: 15px; }

  .closing { font-size: 10.5px; }
  .signature { display: block; margin-top: 8px; width: 130px; height: 42px; }

  .footer-swoosh { position: absolute; left: 0; top: 0; width: 580px; height: 850px; pointer-events: none; }
</style>
</head>
<body>
  <main class="letterhead">
    <header>
      <div class="brand">
        <div class="brand-name">Northvale</div>
        <div class="brand-sub">Realty Group, LLC</div>
        <div class="brand-rule"></div>
      </div>
      <div class="divider"></div>
      <ul class="contact">
        <li>88 Harbor Lane, Suite 210</li>
        <li>Name, NY, USA</li>
        <li><svg viewBox="0 0 10 10"><path d="M2 0h2l1 3-1.5 1a6 6 0 0 0 2.5 2.5L7 5l3 1v2a2 2 0 0 1-2 2A8 8 0 0 1 0 2a2 2 0 0 1 2-2z"/></svg>555-318-2046</li>
        <li><svg viewBox="0 0 10 10"><rect x="0" y="3" width="10" height="7" rx="1"/><rect x="2" y="0" width="6" height="3"/></svg>555-740-6613</li>
        <li><svg viewBox="0 0 10 10"><path d="M0 2h10v6H0z M0 2l5 4 5-4"/></svg>info@northvalerealtyllc.com</li>
        <li><svg viewBox="0 0 10 10"><circle cx="5" cy="5" r="5"/></svg>www.northvalerealtyllc.com</li>
      </ul>
    </header>

    <section class="recipient">
      Mr/s<br>First Name and Last Name<br>Company Name<br>Address
    </section>

    <section class="body-copy">
      <p>Lorem Ipsum is simply dummy text of the printing and typesetting industry. Lorem Ipsum has been the industry's standard dummy text ever since the 1500s, when an unknown printer took a galley of type and scrambled it to make a type specimen book. It has survived not only five centuries, but also the leap into electronic typesetting, remaining essentially unchanged. It was popularised in the 1960s with the release of Typefold sheets containing Lorem Ipsum passages.</p>
      <p>The standard chunk of Lorem Ipsum used since the 1500s is reproduced below for those interested. Sections 1.10.32 and 1.10.33 from "de Rebus Variis Minor" by Aulus Merenda are also reproduced in their exact original form, accompanied by English versions from the 1914 translation by J. Tollerby. Lorem ipsum dolor sit amet, consectetur adipiscing elit, sed do eiusmod tempor incididunt ut labore et dolore magna aliqua.</p>
      <p>It is a long established fact that a reader will be distracted by the readable content of a page when looking at its layout. The point of using Lorem Ipsum is that it has a more-or-less normal distribution of letters, as opposed to using 'Content here, content here', making it look like readable English. Many desktop publishing packages and web page editors now.</p>
      <div class="closing">Your Sincerely,</div>
      <svg class="signature" role="img" aria-label="Handwritten signature" viewBox="0 0 130 42">
        <rect width="130" height="42" rx="4" fill="var(--signature-fill)"/>
      </svg>
    </section>

    <svg class="footer-swoosh" viewBox="0 0 580 850" aria-hidden="true">
      <path d="M330 850 Q480 730 560 560" fill="none" stroke="var(--grey-line)" stroke-width="5"/>
      <path d="M345 850 Q500 740 580 570 L580 850 Z" fill="var(--purple)"/>
    </svg>
  </main>
</body>
</html>
```